Business card for Luxury Portable Restroom Trailer company

We are a Luxury Portable Restroom Trailer Company Called FALCRIDGE HIRES. Based in Orange County California. We provide portable restroom trailers for events, such as, Weddings, Concerts, Charity events, Sporting events, Tournaments, Corporate events, ect. We rent and Sell the Luxury restrooms. Our colors are white, grey, and Orange. As you will see in the logo we uploaded.
There are 2 people in the company so the names and titles will change for the 3 people but card will remain the same. Here is the information for each Person: Dwight Penner CFO 555 318-0476
next Person: Leon Marchetti VP 555 318-0476
Next Person: Owen Marchetti CEO 555 318-0476
Information to include on the card: Luxury Restroom Trailers Rental and Sales. Weddings, Concerts, Charity, Sporting and Corp. Events.

```html
<!DOCTYPE html>
<html lang="en">
<head>
<meta charset="utf-8">
<title>Falcridge Hires – Business Card</title>
<link href="https://fonts.googleapis.com/css2?family=Montserrat:wght@500;700;800&display=swap" rel="stylesheet">
<style>
  :root {
    --orange: #f26a21;
    --grey: #58585a;
    --ink: #2b2b2b;
    --card: #ffffff;
    --backdrop: #cfcfcf;
  }
  * { box-sizing: border-box; margin: 0; padding: 0; }
  html, body { width: 1200px; height: 856px; overflow: hidden; }
  body {
    background: var(--backdrop);
    font-family: "Montserrat", sans-serif;
    display: flex;
    align-items: center;
    justify-content: center;
    gap: 40px;
  }
  .card {
    width: 540px;
    height: 309px;
    background: var(--card);
    box-shadow: 0 10px 28px rgba(0,0,0,0.25);
    position: relative;
  }

  /* Contact side */
  .card--contacts {
    display: flex;
    align-items: center;
    padding: 0 34px 0 40px;
  }
  .brand {
    display: flex;
    align-items: center;
    gap: 10px;
    color: var(--grey);
    font-weight: 800;
    letter-spacing: 0.02em;
    line-height: 1;
  }
  .brand__square {
    width: 14px;
    height: 14px;
    background: var(--orange);
    flex: none;
  }
  .card--contacts .brand { font-size: 21px; width: 230px; }
  .divider {
    width: 2px;
    height: 200px;
    background: var(--orange);
    margin: 0 24px 0 14px;
    flex: none;
  }
  .contacts { display: flex; flex-direction: column; gap: 14px; }
  .contact__name {
    color: var(--orange);
    font-weight: 700;
    font-size: 17px;
    text-transform: uppercase;
    letter-spacing: 0.01em;
  }
  .contact__title {
    color: var(--ink);
    font-weight: 500;
    font-size: 13px;
    margin-top: 3px;
  }
  .contact__phone {
    display: flex;
    align-items: center;
    gap: 7px;
    color: var(--ink);
    font-weight: 500;
    font-size: 13px;
    margin-top: 2px;
  }
  .icon-phone { width: 13px; height: 13px; fill: var(--orange); }

  /* Services side */
  .card--services {
    display: flex;
    flex-direction: column;
    align-items: center;
    justify-content: center;
    gap: 40px;
  }
  .card--services .brand { font-size: 34px; }
  .card--services .brand__square { width: 20px; height: 20px; }
  .services {
    list-style: none;
    display: flex;
    flex-wrap: wrap;
    justify-content: center;
    gap: 8px 16px;
    width: 440px;
    font-size: 14px;
    font-weight: 500;
    color: var(--ink);
  }
  .services li { display: flex; align-items: center; gap: 7px; }
  .services li::before {
    content: "";
    width: 8px;
    height: 8px;
    border-radius: 50%;
    background: var(--orange);
  }
</style>
</head>
<body>
  <section class="card card--contacts">
    <div class="brand"><span class="brand__square"></span>FALCRIDGE HIRES</div>
    <div class="divider"></div>
    <div class="contacts">
      <div class="contact">
        <p class="contact__name">Dwight Penner</p>
        <p class="contact__title">CFO</p>
        <p class="contact__phone"><svg class="icon-phone" viewBox="0 0 24 24"><path d="M6.6 10.8a15.5 15.5 0 0 0 6.6 6.6l2.2-2.2a1 1 0 0 1 1-.25 11.4 11.4 0 0 0 3.6.57 1 1 0 0 1 1 1V20a1 1 0 0 1-1 1A17 17 0 0 1 3 4a1 1 0 0 1 1-1h3.5a1 1 0 0 1 1 1c0 1.25.2 2.45.57 3.57a1 1 0 0 1-.25 1z"/></svg>555 318-0476</p>
      </div>
      <div class="contact">
        <p class="contact__name">Leon Marchetti</p>
        <p class="contact__title">VP</p>
        <p class="contact__phone"><svg class="icon-phone" viewBox="0 0 24 24"><path d="M6.6 10.8a15.5 15.5 0 0 0 6.6 6.6l2.2-2.2a1 1 0 0 1 1-.25 11.4 11.4 0 0 0 3.6.57 1 1 0 0 1 1 1V20a1 1 0 0 1-1 1A17 17 0 0 1 3 4a1 1 0 0 1 1-1h3.5a1 1 0 0 1 1 1c0 1.25.2 2.45.57 3.57a1 1 0 0 1-.25 1z"/></svg>555 318-0476</p>
      </div>
      <div class="contact">
        <p class="contact__name">Owen Marchetti</p>
        <p class="contact__title">CEO</p>
        <p class="contact__phone"><svg class="icon-phone" viewBox="0 0 24 24"><path d="M6.6 10.8a15.5 15.5 0 0 0 6.6 6.6l2.2-2.2a1 1 0 0 1 1-.25 11.4 11.4 0 0 0 3.6.57 1 1 0 0 1 1 1V20a1 1 0 0 1-1 1A17 17 0 0 1 3 4a1 1 0 0 1 1-1h3.5a1 1 0 0 1 1 1c0 1.25.2 2.45.57 3.57a1 1 0 0 1-.25 1z"/></svg>555 318-0476</p>
      </div>
    </div>
  </section>

  <section class="card card--services">
    <div class="brand"><span class="brand__square"></span>FALCRIDGE HIRES</div>
    <ul class="services">
      <li>Luxury Restroom Trailers Rental and Sales</li>
      <li>Weddings</li>
      <li>Concerts</li>
      <li>Charity</li>
      <li>Sporting and Corp</li>
      <li>Events</li>
    </ul>
  </section>
</body>
</html>
```